Ledger Lanternfox Powerpoint with Marshal Valorline Type Theme

Need powerpoint template with matching colors and different slide options. Logo and colors to be used can be found at ledgerlanternfox.example. Want brightly colored slide deck that is readable form the back of a room, but highlights colors. I will be incorporating Quizzap into the slides to gamify my presentations.

Target Market(s)

Tech

Industry/Entity Type

IT, specifically database, but crossing over to mental health in IT, important note this is not for a company, this is just for a professional building a brand

Font styles to use
Sans Serif

Colors
0054AA
0677BA
7BADD7
CADEEF
E8F1F8
EB3D1F
EC4F4E
F09395
F8D3D4
FCEDEE

Requirements
Must have
• My Logo in the bottom corner, front page, a thank your page, question page, content page, content page with two columns, content page with graphs, and icons to be used in the primary colors of the logos, About Me Page, Break Slides, Demo break slide
Should not have
• Lighter shades of colors, I want to pop out where colors are used, I want spacing and font size to be readable from the back of a room, most likely black text and white background

```html
<!DOCTYPE html>
<html lang="en">
<head>
<meta charset="utf-8">
<title>Ledger Lanternfox – Marshal Valorline Slide Deck</title>
<link rel="stylesheet" href="https://fonts.googleapis.com/css2?family=Poppins:wght@300;400;500;600;700&display=swap">
<style>
:root{
  --navy:#1d4386;
  --navy-deep:#16366f;
  --red:#e8262b;
  --grey:#7d7d7d;
  --ink:#2b2b2b;
  --muted:#666;
  --page:#dcdcdc;
  --white:#fff;
  --faint:#e8eef7;
}
*{margin:0;padding:0;box-sizing:border-box}
html,body{width:1200px;height:2274px;overflow:hidden;background:var(--page)}
body{font-family:'Poppins',sans-serif;color:var(--ink)}
.deck{display:grid;grid-template-columns:repeat(3,388px);grid-auto-rows:217px;gap:9px 8px;padding:11px}
.slide{position:relative;width:388px;height:217px;background:var(--white);overflow:hidden}
.a{position:absolute}
.tx{font-size:4px;line-height:1.4;color:var(--muted)}
.tx-w{font-size:4px;line-height:1.4;color:#fff}
.title{font-weight:600;color:var(--navy);font-size:16px;line-height:1.1}
.center{text-align:center}
.bar{width:16px;height:3px;background:var(--red)}
.brand-dot{left:5px;top:5px;width:9px;height:9px;border-radius:50%;background:var(--navy)}
.brand-side{left:7px;top:86px;writing-mode:vertical-rl;transform:rotate(180deg);font-size:5px;font-weight:700;color:var(--red);letter-spacing:.2px}
.pg{left:10px;bottom:5px;font-size:4px;color:var(--muted)}
.brand{font-weight:700;color:#fff;display:flex;align-items:center;gap:4px;white-space:nowrap}
.brand i{display:inline-block;border-radius:50%;background:var(--red)}
.brand-navy{color:var(--navy)}
.photo-blue{background:linear-gradient(135deg,#27508f,#1a3c78 60%,#15326a)}
.pill{background:var(--red);color:#fff;border-radius:10px;text-align:center;font-weight:500}
.card{color:#fff;text-align:center;border-radius:2px}
.icon-ring{width:22px;height:22px;border-radius:50%;background:#fff;border:1px solid #ddd}
.proj{font-size:5px;font-weight:600;color:var(--ink)}
table.chart{border-collapse:collapse;font-size:3.6px}
table.chart td{height:14.5px;border-bottom:1px solid #eee;text-align:center;color:var(--muted)}
table.chart td.lbl{background:var(--navy);color:#fff;font-weight:600;text-align:left;padding-left:9px;border-bottom:1px solid #fff;width:94px}
table.chart th{background:var(--red);color:#fff;font-weight:500;height:13px;width:59px}
.q{width:14px;height:14px;border-radius:2px;color:#fff;font-weight:600;font-size:8px;text-align:center;line-height:14px}
.chev{height:24px;color:#fff;font-size:6px;font-weight:600;display:flex;align-items:center;justify-content:center;clip-path:polygon(0 0,85% 0,100% 50%,85% 100%,0 100%,15% 50%)}
</style>
</head>
<body>
<main class="deck">

<!-- 1 cover -->
<section class="slide photo-blue" role="img" aria-label="Cover slide over a photo of a person working on a tablet">
  <div class="a brand" style="left:150px;top:42px;font-size:9px"><i style="width:10px;height:10px"></i>Ledger Lanternfox</div>
  <div class="a" style="left:118px;top:72px;width:152px;height:9px;border-radius:5px;background:rgba(255,255,255,.15);color:#dbe4f2;font-size:4.5px;text-align:center;line-height:9px;letter-spacing:1px">www.websitename.com</div>
  <div class="a center" style="left:0;width:388px;top:86px;color:#fff;font-weight:600;font-size:23px;line-height:1.02">Presentation<br>Title Goes Here</div>
  <div class="a center" style="left:0;width:388px;top:138px;color:#e6ecf5;font-size:8px;font-weight:300">Sub Title Goes Here</div>
  <div class="a pill" style="left:146px;top:177px;width:84px;height:12px;font-size:5px;line-height:12px">Oct 2021</div>
</section>

<!-- 2 title -->
<section class="slide">
  <div class="a" style="left:0;top:0;width:388px;height:182px;background:var(--navy)"></div>
  <div class="a" style="left:19px;top:70px;color:#fff;font-size:19px;font-weight:500;line-height:1.3">TITLE OF<br>PRESENTATION</div>
  <div class="a tx-w" style="left:21px;top:138px;font-size:5px">Here is A place for Credentials<br>Date: 2021 March</div>
  <div class="a brand brand-navy" style="left:10px;top:195px;font-size:8px"><i style="width:9px;height:9px;background:var(--navy)"></i>Ledger Lanternfox</div>
  <div class="a" style="left:308px;top:199px;font-size:5px;font-weight:600;color:var(--navy)">Presenter Name</div>
</section>

<!-- 3 title over photo -->
<section class="slide photo-blue" role="img" aria-label="Title slide over a photo of server racks">
  <div class="a brand" style="left:24px;top:60px;font-size:7px"><i style="width:8px;height:8px"></i>Ledger Lanternfox</div>
  <div class="a" style="left:23px;top:83px;color:#fff;font-size:19px;font-weight:500;line-height:1.3">TITLE OF<br>PRESENTATION</div>
  <div class="a tx-w" style="left:25px;top:152px;font-size:5px">Here is A place for Credentials<br>Date: 2021 March</div>
</section>

<!-- 4 diagonal cover -->
<section class="slide" style="background:var(--navy)">
  <svg class="a" style="left:0;top:0" width="388" height="217" viewBox="0 0 388 217">
    <polygon points="215,0 388,0 388,217 120,217" fill="#cfd6df" role="img" aria-label="Photo of a laptop on a desk"/>
    <polygon points="128,113 388,113 388,170 105,170" fill="var(--red)"/>
  </svg>
  <div class="a brand" style="left:45px;top:52px;font-size:11px"><i style="width:14px;height:14px"></i>Ledger Lanternfox</div>
  <div class="a center" style="left:150px;width:220px;top:120px;color:#fff;font-size:19px;font-weight:600;line-height:1">Presentation<br>Title Goes Here</div>
</section>

<!-- 5 white cover -->
<section class="slide">
  <div class="a brand brand-navy" style="left:25px;top:45px;font-size:8px"><i style="width:10px;height:10px;background:var(--navy)"></i>Ledger Lanternfox</div>
  <div class="a" style="left:24px;top:83px;color:var(--navy);font-size:23px;font-weight:600;line-height:1.02">Presentation<br>Title Goes Here</div>
  <div class="a" style="left:25px;top:133px;color:var(--red);font-size:8px">Sub Title Goes Here</div>
  <div class="a pill" style="left:25px;top:172px;width:115px;height:12px;font-size:5px;line-height:12px;letter-spacing:1px">www.websitename.com</div>
</section>

<!-- 6 about me -->
<section class="slide">
  <div class="a brand-dot"></div><div class="a brand-side">Ledger Lanternfox</div><div class="a pg">6</div>
  <svg class="a" style="left:32px;top:38px" width="90" height="90" viewBox="0 0 90 90"><path d="M10 70 A40 40 0 0 1 45 5" stroke="var(--navy)" stroke-width="6" fill="none"/></svg>
  <div class="a" role="img" aria-label="Portrait photo of the presenter" style="left:42px;top:48px;width:76px;height:76px;border-radius:50%;background:linear-gradient(#555,#222)"></div>
  <div class="a tx" style="left:55px;top:144px;color:var(--red);line-height:3.4"><span style="color:var(--navy)">■</span> Here is a place for text<br><span style="color:var(--navy)">●</span> Here is a place for text<br><span style="color:var(--navy)">■</span> Here is a place for text</div>
  <div class="a" style="left:170px;top:32px;font-size:8px;color:var(--red);font-weight:300">Manager</div>
  <div class="a" style="left:170px;top:41px;font-size:15px;color:var(--navy);font-weight:500">Name, Last Name</div>
  <div class="a bar" style="left:171px;top:62px"></div>
  <div class="a tx" style="left:171px;top:70px;width:190px;text-align:justify"><b style="color:var(--red)">A short line about who I am and what I do.</b> I build database systems and help IT teams stay healthy, focused and calm under pressure. I share practical tips on data, tooling and the people who keep systems running every day.<br><br>My talks blend hands-on database work with real stories about stress, balance and wellbeing in tech. Expect clear lessons, live examples and quick quizzes that keep the whole room involved.</div>
</section>

<!-- 7 welcome -->
<section class="slide">
  <div class="a brand-dot"></div><div class="a brand-side">Ledger Lanternfox</div><div class="a pg">7</div>
  <div class="a" role="img" aria-label="Portrait photo of the speaker" style="left:45px;top:54px;width:110px;height:110px;border-radius:10px;background:linear-gradient(#4a4a4a,#1e1e1e)"></div>
  <div class="a" style="left:74px;top:143px;width:101px;height:14px;background:var(--red);color:#fff;font-size:8px;font-weight:500;text-align:center;line-height:14px">Your Name</div>
  <div class="a title" style="left:193px;top:33px;font-size:15px">Welcome Message</div>
  <div class="a" style="left:188px;top:62px;font-size:30px;color:#ddd;line-height:1">“</div>
  <div class="a tx center" style="left:193px;top:75px;width:176px">Welcome to this session. Today we explore how better data habits and a healthier team culture go hand in hand, with quick quizzes along the way.</div>
  <div class="a tx" style="left:193px;top:126px;width:176px;text-align:justify">Thanks for joining. We will cover real database problems, the pressure they put on people, and simple steps that help. Ask questions at any time, join the live quiz rounds and take away ideas you can use at work tomorrow. Every section ends with a short recap so nothing gets lost.</div>
</section>

<!-- 8 title and body -->
<section class="slide">
  <div class="a brand-dot"></div><div class="a brand-side">Ledger Lanternfox</div><div class="a pg">8</div>
  <div class="a title" style="left:34px;top:22px">Title And Body Slide</div>
  <div class="a bar" style="left:35px;top:41px"></div>
</section>

<!-- 9 title and long body -->
<section class="slide">
  <div class="a brand-dot"></div><div class="a brand-side">Ledger Lanternfox</div>
  <div class="a title" style="left:34px;top:22px">Title And Body Slide</div>
  <div class="a bar" style="left:35px;top:41px"></div>
  <div class="a tx" style="left:38px;top:66px;width:327px;text-align:justify">Body text goes here. Keep each paragraph short and focused so it can be read clearly from the back of the room, with one main idea per block and plenty of space around it for breathing room.<br><br>Use this second paragraph to give supporting detail, an example from real work, or a number that matters. Break long thoughts into smaller points and let the heading carry the main message for the audience.<br><br>A final paragraph can wrap up the idea, link it to the next slide, or invite the audience into a quick quiz question. Simple language and a steady rhythm keep attention high. Keep the tone friendly and direct, give people time to read, and pause before moving on so the point lands with everyone in the room before the next topic starts.</div>
</section>

<!-- 10 slide break -->
<section class="slide">
  <div class="a" style="left:0;top:0;width:388px;height:5px;background:var(--navy)"></div>
  <div class="a" style="left:15px;top:44px;font-size:50px;font-weight:300;color:#e3e7ee;line-height:1">01</div>
  <div class="a" style="left:36px;top:66px;font-size:28px;font-weight:300;color:var(--navy);line-height:.95">Slide<br>Break</div>
  <div class="a tx" style="left:36px;top:133px;width:165px;color:var(--navy)">A short note about the next section. Set the scene, name the topic and give a hint of what comes next so the room is ready.</div>
  <div class="a brand brand-navy" style="left:228px;top:102px;font-size:10px"><i style="width:14px;height:14px;background:var(--navy)"></i>Ledger Lanternfox</div>
  <div class="a" style="left:0;top:208px;width:388px;height:9px;background:var(--red)"></div>
</section>

<!-- 11 demo circle -->
<section class="slide photo-blue" role="img" aria-label="Demo break over a photo of hands on a tablet">
  <div class="a" style="left:104px;top:19px;width:180px;height:180px;border-radius:50%;border:1px solid #fff"></div>
  <div class="a center" style="left:0;width:388px;top:47px;color:var(--red);font-size:14px;font-weight:600">— DEMO —</div>
  <div class="a tx-w center" style="left:122px;top:73px;width:144px;font-size:5px">Live demo time. Watch the steps on screen, then try them on your own setup. We pause between each stage so you can follow along, ask questions and check your results with the rest of the group before we move on to the next part of the session.</div>
</section>

<!-- 12 demo band -->
<section class="slide photo-blue" role="img" aria-label="Demo break over a photo of a server room">
  <div class="a" style="left:21px;top:26px;width:346px;height:1px;background:rgba(255,255,255,.3)"></div>
  <div class="a" style="left:21px;top:191px;width:346px;height:1px;background:rgba(255,255,255,.3)"></div>
  <div class="a brand" style="left:22px;top:101px;font-size:8px"><i style="width:10px;height:10px"></i>Ledger Lanternfox</div>
  <div class="a" style="left:149px;top:68px;width:2px;height:85px;background:var(--red)"></div>
  <div class="a pill" style="left:165px;top:68px;width:76px;height:16px;font-size:10px;line-height:16px;font-weight:600">DEMO</div>
  <div class="a tx-w" style="left:166px;top:96px;width:180px;font-size:6px">Live demo time. Follow each step on screen and try it on your own setup. We pause after every stage for questions and checks.</div>
</section>

<!-- 13 pic and text -->
<section class="slide">
  <div class="a brand-dot"></div><div class="a brand-side">Ledger Lanternfox</div><div class="a pg">13</div>
  <div class="a title" style="left:39px;top:63px;font-size:18px">Pic And Text</div>
  <div class="a bar" style="left:39px;top:85px"></div>
  <div class="a tx" style="left:39px;top:94px;width:136px;text-align:justify">Pair one strong photo with a few lines of text. Explain what the audience sees, why it matters, and how it links to the main point. Keep sentences short, use plain words and leave enough white space so the image and the message both stand out clearly.</div>
  <div class="a" style="left:191px;top:28px;width:128px;height:94px;background:var(--red)"></div>
  <div class="a" role="img" aria-label="Photo of a desk with a monitor, keyboard and hands typing" style="left:212px;top:49px;width:170px;height:143px;background:linear-gradient(135deg,#6f7c8e,#b8c2cf);box-shadow:0 3px 8px rgba(0,0,0,.2)"></div>
</section>

<!-- 14 quote photo -->
<section class="slide">
  <div class="a" role="img" aria-label="Photo of a hiker standing on a mountain peak" style="left:0;top:0;width:168px;height:217px;background:linear-gradient(#7f8a95,#3a3f45)"></div>
  <div class="a" style="left:192px;top:66px;width:170px;font-size:8.5px;font-weight:600;color:var(--navy);line-height:1.25">Success is not only what you achieve in your life, but also what you inspire in the lives of others</div>
  <div class="a" style="left:87px;top:143px;width:301px;height:74px;background:var(--navy);border-radius:8px 0 0 0"></div>
  <div class="a tx-w" style="left:112px;top:160px;width:75px"><b style="font-size:5px">Lorem ipsum dolor</b><br><br>Short supporting line for this first point here.</div>
  <div class="a tx-w" style="left:204px;top:158px;width:75px"><b style="font-size:5px">Lorem ipsum dolor</b><br><br>Short supporting line for this second point here.</div>
  <div class="a tx-w" style="left:299px;top:158px;width:75px"><b style="font-size:5px">Lorem ipsum dolor</b><br><br>Short supporting line for this third point here.</div>
</section>

<!-- 15 awesome text -->
<section class="slide">
  <div class="a brand-dot"></div><div class="a brand-side">Ledger Lanternfox</div><div class="a pg">15</div>
  <div class="a" style="left:23px;top:0;width:365px;height:112px;background:var(--navy)"></div>
  <div class="a center" style="left:23px;width:365px;top:30px;color:#fff;font-size:16px;font-weight:500">Here Add Awesome Text</div>
  <div class="a bar" style="left:197px;top:54px"></div>
  <svg class="a" style="left:0;top:0" width="388" height="217" viewBox="0 0 388 217">
    <g fill="var(--red)" stroke="#fff" stroke-width="1.5"><circle cx="96" cy="107" r="20"/><circle cx="204" cy="107" r="20"/><circle cx="313" cy="107" r="20"/></g>
    <g stroke="#fff" stroke-width="1.2" fill="none"><circle cx="96" cy="107" r="7"/><circle cx="96" cy="107" r="3"/><path d="M199 113 L210 101 M203 101 h7 v7"/><path d="M306 113 v-5 M311 113 v-9 M316 113 v-7 M321 113 v-12"/></g>
  </svg>
  <div class="a proj center" style="left:56px;width:80px;top:137px">Project name</div>
  <div class="a proj center" style="left:164px;width:80px;top:137px">Project name</div>
  <div class="a proj center" style="left:273px;width:80px;top:137px">Project name</div>
  <div class="a tx center" style="left:51px;width:90px;top:148px">Short note that explains this first project in a few simple words.</div>
  <div class="a tx center" style="left:159px;width:90px;top:148px">Short note that explains this second project in a few simple words.</div>
  <div class="a tx center" style="left:268px;width:90px;top:148px">Short note that explains this third project in a few simple words.</div>
</section>

<!-- 16 three columns -->
<section class="slide">
  <div class="a brand-dot"></div><div class="a brand-side">Ledger Lanternfox</div><div class="a pg">16</div>
  <div class="a title center" style="left:0;width:388px;top:23px">3 Columns Slide</div>
  <div class="a bar" style="left:186px;top:44px"></div>
  <div class="a card" style="left:53px;top:90px;width:89px;height:78px;background:var(--red)"></div>
  <div class="a card" style="left:152px;top:90px;width:89px;height:78px;background:var(--navy)"></div>
  <div class="a card" style="left:251px;top:90px;width:89px;height:78px;background:var(--grey)"></div>
  <div class="a icon-ring" style="left:86px;top:79px"></div>
  <div class="a icon-ring" style="left:185px;top:79px"></div>
  <div class="a icon-ring" style="left:284px;top:79px"></div>
  <svg class="a" style="left:0;top:0" width="388" height="217"><g fill="none" stroke-width="1"><circle cx="97" cy="90" r="5" stroke="var(--red)"/><circle cx="196" cy="90" r="5" stroke="var(--navy)"/><circle cx="196" cy="90" r="2" stroke="var(--navy)"/><circle cx="295" cy="90" r="5" stroke="var(--grey)"/><path d="M290 90 h10 M295 85 v10" stroke="var(--grey)"/></g></svg>
  <div class="a tx-w center" style="left:58px;width:79px;top:117px"><b style="font-size:4.8px">Project name here</b><br><br>Brief detail for the first column, kept short and easy to read.</div>
  <div class="a tx-w center" style="left:157px;width:79px;top:117px"><b style="font-size:4.8px">Project name here</b><br><br>Brief detail for the second column, kept short and easy to read.</div>
  <div class="a tx-w center" style="left:256px;width:79px;top:117px"><b style="font-size:4.8px">Project name here</b><br><br>Brief detail for the third column, kept short and easy to read.</div>
</section>

<!-- 17 screenshot -->
<section class="slide">
  <div class="a brand-dot"></div><div class="a brand-side">Ledger Lanternfox</div><div class="a pg">17</div>
  <svg class="a" style="left:0;top:0" width="388" height="217" viewBox="0 0 388 217">
    <polygon points="23,0 160,0 290,217 23,217" fill="var(--navy)"/>
    <rect x="174" y="48" width="208" height="133" rx="4" fill="#1f1f1f"/>
    <rect x="180" y="54" width="196" height="121" fill="#9a9a9a"/>
    <rect x="150" y="181" width="238" height="6" rx="2" fill="#c9c9c9"/>
  </svg>
  <div class="a center" style="left:180px;width:196px;top:111px;color:#fff;font-size:6px;font-weight:600">HERE YOU CAN ADD A SCREENSHOT</div>
  <div class="a" style="left:43px;top:74px;color:#fff;font-size:15px;font-weight:500;line-height:1.3">A Place for<br>Screenshot</div>
  <div class="a tx-w" style="left:44px;top:126px;width:116px">Describe what the screenshot shows and point out the detail the audience should notice first.</div>
</section>

<!-- 18 six columns -->
<section class="slide">
  <div class="a brand-dot"></div><div class="a brand-side">Ledger Lanternfox</div><div class="a pg">18</div>
  <div class="a title center" style="left:0;width:388px;top:18px">6 Columns Slide</div>
  <div class="a bar" style="left:186px;top:39px"></div>
  <svg class="a" style="left:0;top:0" width="388" height="217"><g fill="none" stroke="var(--navy)" stroke-width=".9">
    <rect x="42" y="77" width="10" height="11"/><path d="M44 81h6M44 84h6"/>
    <rect x="210" y="77" width="10" height="11"/><path d="M212 81h6M212 84h6"/>
    <path d="M42 129h11M44 127v-3M47 127v-5M50 127v-7"/><path d="M210 129h11M212 127v-3M215 127v-5M218 127v-7"/>
    <circle cx="47" cy="165" r="5"/><circle cx="215" cy="165" r="5"/><path d="M44 165h6M212 165h6"/></g></svg>
  <div class="a tx" style="left:70px;top:73px;width:105px"><b class="proj" style="font-size:4.5px">Project name</b><br>Short description for this item in one or two lines.</div>
  <div class="a tx" style="left:238px;top:73px;width:105px"><b class="proj" style="font-size:4.5px">Project name</b><br>Short description for this item in one or two lines.</div>
  <div class="a tx" style="left:70px;top:114px;width:105px"><b class="proj" style="font-size:4.5px">Project name</b><br>Short description for this item in one or two lines.</div>
  <div class="a tx" style="left:238px;top:114px;width:105px"><b class="proj" style="font-size:4.5px">Project name</b><br>Short description for this item in one or two lines.</div>
  <div class="a tx" style="left:70px;top:155px;width:105px"><b class="proj" style="font-size:4.5px">Project name</b><br>Short description for this item in one or two lines.</div>
  <div class="a tx" style="left:238px;top:155px;width:105px"><b class="proj" style="font-size:4.5px">Project name</b><br>Short description for this item in one or two lines.</div>
</section>

<!-- 19 chart table -->
<section class="slide">
  <div class="a brand-dot"></div><div class="a brand-side">Ledger Lanternfox</div><div class="a pg">19</div>
  <div class="a title center" style="left:0;width:388px;top:17px">Chart Slide</div>
  <div class="a bar" style="left:186px;top:38px"></div>
  <table class="a chart" style="left:30px;top:51px;width:332px">
    <tr><td style="border:0"></td><th>Your Text Here</th><th>Your Text Here</th><th>Your Text Here</th><th>Your Text Here</th></tr>
    <tr><td class="lbl">You can replace this text</td><td>1250</td><td style="color:var(--navy);font-size:8px">✔</td><td>50%</td><td>1250</td></tr>
    <tr><td class="lbl">You can replace this text</td><td>3623</td><td style="color:var(--navy);font-size:8px">✖</td><td>50%</td><td>3623</td></tr>
    <tr><td class="lbl">You can replace this text</td><td>2569</td><td style="color:var(--navy);font-size:8px">✔</td><td>12%</td><td>2569</td></tr>
    <tr><td class="lbl">You can replace this text</td><td>1020</td><td style="color:var(--navy);font-size:8px">✖</td><td>65%</td><td>1020</td></tr>
    <tr><td class="lbl">You can replace this text</td><td>2320</td><td style="color:var(--navy);font-size:8px">✔</td><td>36%</td><td>2320</td></tr>
    <tr><td class="lbl">You can replace this text</td><td>5698</td><td style="color:var(--navy);font-size:8px">✖</td><td>95%</td><td>5698</td></tr>
    <tr><td class="lbl">You can replace this text</td><td>1999</td><td style="color:var(--navy);font-size:8px">✖</td><td>66%</td><td>1999</td></tr>
  </table>
</section>

<!-- 20 smart art -->
<section class="slide">
  <div class="a brand-dot"></div><div class="a brand-side">Ledger Lanternfox</div><div class="a pg">20</div>
  <div class="a title" style="left:34px;top:21px">Smart Art Slide</div>
  <div class="a bar" style="left:35px;top:40px"></div>
  <svg class="a" style="left:0;top:0" width="388" height="217"><g fill="none" stroke="var(--grey)" stroke-width=".9"><circle cx="43" cy="82" r="5"/><path d="M39 127 l8-8 M44 119h3v3"/><rect x="39" y="164" width="8" height="8"/></g>
    <polygon points="286,50 322,88 286,124 250,88" fill="var(--navy)"/>
    <polygon points="248,93 282,127 268,160 215,160" fill="var(--red)"/>
    <polygon points="324,93 290,127 304,160 357,160" fill="var(--grey)"/></svg>
  <div class="a tx" style="left:55px;top:75px;width:118px"><b style="color:var(--navy);font-size:4.8px">Lorem ipsum dolor</b><br>A short line that explains this first step clearly.</div>
  <div class="a tx" style="left:55px;top:118px;width:118px"><b style="color:var(--navy);font-size:4.8px">Lorem ipsum dolor</b><br>A short line that explains this second step clearly.</div>
  <div class="a tx" style="left:55px;top:162px;width:118px"><b style="color:var(--navy);font-size:4.8px">Lorem ipsum dolor</b><br>A short line that explains this third step clearly.</div>
  <div class="a tx-w center" style="left:262px;width:48px;top:74px"><b style="font-size:4.5px">Project name</b><br>Short text for this part.</div>
  <div class="a tx-w center" style="left:228px;width:50px;top:136px"><b style="font-size:4.5px">Project name</b><br>Short text here.</div>
  <div class="a tx-w center" style="left:296px;width:50px;top:136px"><b style="font-size:4.5px">Project name</b><br>Short text here.</div>
</section>

<!-- 21 quotes -->
<section class="slide">
  <div class="a brand-dot"></div><div class="a brand-side">Ledger Lanternfox</div><div class="a pg">21</div>
  <div class="a title center" style="left:0;width:388px;top:17px">Here is Quotes</div>
  <div class="a bar" style="left:186px;top:38px"></div>
  <div class="a" style="left:37px;top:52px;font-size:26px;font-weight:700;color:var(--red);line-height:1">”</div>
  <div class="a" style="left:215px;top:52px;font-size:26px;font-weight:700;color:var(--navy);line-height:1">”</div>
  <div class="a tx" style="left:37px;top:89px;width:145px;font-size:5.2px">A good quote says in one line what a whole slide of text cannot. Pick words that stay with the room long after.</div>
  <div class="a tx" style="left:215px;top:89px;width:145px;font-size:5.2px">A good quote says in one line what a whole slide of text cannot. Pick words that stay with the room long after.</div>
  <div class="a" style="left:37px;top:156px;width:18px;height:18px;border-radius:50%;background:#ccc"></div>
  <div class="a" style="left:215px;top:156px;width:18px;height:18px;border-radius:50%;background:#ccc"></div>
  <div class="a tx" style="left:64px;top:158px"><b style="color:var(--navy);font-size:5px">Your Name</b><br>Founder</div>
  <div class="a tx" style="left:242px;top:158px"><b style="color:var(--navy);font-size:5px">Your Name</b><br>Founder</div>
</section>

<!-- 22 statistics circles -->
<section class="slide">
  <div class="a brand-dot"></div><div class="a brand-side">Ledger Lanternfox</div><div class="a pg">22</div>
  <div class="a title center" style="left:0;width:388px;top:20px">Here Is Statistics</div>
  <div class="a bar" style="left:186px;top:41px"></div>
  <svg class="a" style="left:0;top:0" width="388" height="217">
    <circle cx="91" cy="127" r="57" fill="var(--navy)"/>
    <circle cx="91" cy="148" r="36" fill="var(--red)"/>
    <circle cx="91" cy="167" r="17" fill="var(--grey)"/>
    <g fill="#fff" font-size="13" font-weight="600" font-family="Poppins,sans-serif" text-anchor="middle"><text x="91" y="100">$</text><text x="91" y="137">$</text><text x="91" y="172">$</text></g>
    <g stroke="#999" stroke-width=".5"><line x1="110" y1="92" x2="168" y2="92"/><line x1="120" y1="127" x2="168" y2="127"/><line x1="108" y1="167" x2="168" y2="167"/></g>
    <g fill="var(--navy)" font-size="9" font-weight="600" font-family="Poppins,sans-serif"><text x="172" y="95">5M</text><text x="172" y="130">2M</text><text x="172" y="170">1M</text></g>
    <rect x="222" y="90" width="12" height="12" fill="var(--navy)"/><rect x="222" y="125" width="12" height="12" fill="var(--red)"/><rect x="222" y="160" width="12" height="12" fill="var(--grey)"/>
    <g stroke="#fff" stroke-width="1.3" fill="none"><path d="M225 96l2 2 4-4M225 131l2 2 4-4M225 166l2 2 4-4"/></g>
  </svg>
  <div class="a tx" style="left:245px;top:86px;width:115px"><b style="color:var(--navy);font-size:5px">Lorem ipsum dolor</b><br>Short note on what this figure means.</div>
  <div class="a tx" style="left:245px;top:121px;width:115px"><b style="color:var(--navy);font-size:5px">Lorem ipsum dolor</b><br>Short note on what this figure means.</div>
  <div class="a tx" style="left:245px;top:156px;width:115px"><b style="color:var(--navy);font-size:5px">Lorem ipsum dolor</b><br>Short note on what this figure means.</div>
</section>

<!-- 23 progress rings -->
<section class="slide">
  <div class="a brand-dot"></div><div class="a brand-side">Ledger Lanternfox</div><div class="a pg">23</div>
  <div class="a title center" style="left:0;width:388px;top:20px">Here Add Your Title</div>
  <div class="a bar" style="left:186px;top:41px"></div>
  <div class="a tx center" style="left:74px;width:240px;top:60px">A short opening line sets up these three numbers. Say what they measure, where they come from and why the audience should care about them today.</div>
  <svg class="a" style="left:0;top:0" width="388" height="217"><g fill="none" stroke-width="3">
    <circle cx="110" cy="131" r="26" stroke="#ececec"/><circle cx="110" cy="131" r="26" stroke="var(--red)" stroke-dasharray="81.7 163.4" transform="rotate(-90 110 131)"/>
    <circle cx="192" cy="131" r="26" stroke="#ececec"/><circle cx="192" cy="131" r="26" stroke="var(--red)" stroke-dasharray="122.5 163.4" transform="rotate(-90 192 131)"/>
    <circle cx="273" cy="131" r="26" stroke="#ececec"/><circle cx="273" cy="131" r="26" stroke="var(--red)" stroke-dasharray="65.3 163.4" transform="rotate(-90 273 131)"/></g>
    <g fill="var(--navy)" font-size="11" font-weight="600" font-family="Poppins,sans-serif" text-anchor="middle"><text x="110" y="135">50%</text><text x="192" y="135">75%</text><text x="273" y="135">40%</text></g></svg>
  <div class="a tx center" style="left:80px;width:60px;top:164px">Short label for this value</div>
  <div class="a tx center" style="left:162px;width:60px;top:164px">Short label for this value</div>
  <div class="a tx center" style="left:243px;width:60px;top:164px">Short label for this value</div>
</section>

<!-- 24 line chart -->
<section class="slide">
  <div class="a brand-dot"></div><div class="a brand-side">Ledger Lanternfox</div><div class="a pg">24</div>
  <div class="a title center" style="left:0;width:388px;top:17px">Here is Statistics</div>
  <div class="a bar" style="left:186px;top:38px"></div>
  <div class="a" style="left:29px;top:67px;width:93px;height:56px;background:var(--navy);color:#fff;text-align:center;padding-top:14px;font-size:14px;font-weight:300;line-height:1">$0.5M<div style="font-size:4px;margin-top:4px">Revenue</div></div>
  <div class="a" style="left:29px;top:123px;width:93px;height:56px;background:#fff;box-shadow:0 1px 4px rgba(0,0,0,.15);color:var(--red);text-align:center;padding-top:16px;font-size:13px;font-weight:300;line-height:1">-0.28%<div style="font-size:4px;margin-top:4px">Revenue</div></div>
  <svg class="a" style="left:0;top:0" width="388" height="217" font-family="Poppins,sans-serif">
    <g font-size="3.5" fill="#777" text-anchor="end"><text x="150" y="73">$350,000</text><text x="150" y="88">$300,000</text><text x="150" y="102">$250,000</text><text x="150" y="117">$200,000</text><text x="150" y="131">$150,000</text><text x="150" y="146">$100,000</text><text x="150" y="160">$50,000</text><text x="150" y="174">$-</text></g>
    <line x1="154" y1="174" x2="365" y2="174" stroke="#ccc" stroke-width=".5"/>
    <g font-size="3.5" fill="#777" text-anchor="middle"><text x="161" y="182">Jan</text><text x="177" y="182">Feb</text><text x="193" y="182">Mar</text><text x="209" y="182">Apr</text><text x="225" y="182">May</text><text x="241" y="182">Jun</text><text x="257" y="182">Jul</text><text x="273" y="182">Aug</text><text x="289" y="182">Sep</text><text x="305" y="182">Oct</text><text x="321" y="182">Nov</text><text x="337" y="182">Dec</text><text x="353" y="182">Jan</text></g>
    <path d="M161 170 C175 168 185 162 195 145 C200 135 205 125 212 132 C218 138 222 128 230 133 C238 138 244 124 250 128 C258 134 262 150 272 150 C282 150 290 112 300 116 C308 120 306 150 312 150 C320 150 322 120 332 118 C342 116 350 100 362 82" fill="none" stroke="var(--red)" stroke-width="1"/>
  </svg>
</section>

<!-- 25 timeline -->
<section class="slide">
  <div class="a brand-dot"></div><div class="a brand-side">Ledger Lanternfox</div><div class="a pg">25</div>
  <div class="a title center" style="left:0;width:388px;top:20px">Company Timeline</div>
  <div class="a bar" style="left:186px;top:41px"></div>
  <div class="a chev" style="left:36px;top:73px;width:72px;background:var(--red)">STEP 01</div>
  <div class="a chev" style="left:98px;top:73px;width:72px;background:var(--navy)">STEP 02</div>
  <div class="a chev" style="left:160px;top:73px;width:72px;background:var(--red)">STEP 03</div>
  <div class="a chev" style="left:222px;top:73px;width:72px;background:var(--navy)">STEP 04</div>
  <div class="a chev" style="left:284px;top:73px;width:72px;background:var(--red)">STEP 05</div>
  <svg class="a" style="left:0;top:0" width="388" height="217"><g stroke="#bbb" stroke-width=".5" fill="#fff"><line x1="36" y1="117" x2="356" y2="117"/><path d="M68 117v14M132 117v14M196 117v14M260 117v14M323 117v14"/><circle cx="68" cy="131" r="1.5"/><circle cx="132" cy="131" r="1.5"/><circle cx="196" cy="131" r="1.5"/><circle cx="260" cy="131" r="1.5"/><circle cx="323" cy="131" r="1.5"/></g></svg>
  <div class="a tx center" style="left:41px;width:55px;top:146px"><b class="proj">Project name</b><br><br>A short note on what happened at this step.</div>
  <div class="a tx center" style="left:105px;width:55px;top:146px"><b class="proj">Project name</b><br><br>A short note on what happened at this step.</div>
  <div class="a tx center" style="left:169px;width:55px;top:146px"><b class="proj">Project name</b><br><br>A short note on what happened at this step.</div>
  <div class="a tx center" style="left:232px;width:55px;top:146px"><b class="proj">Project name</b><br><br>A short note on what happened at this step.</div>
  <div class="a tx center" style="left:295px;width:55px;top:146px"><b class="proj">Project name</b><br><br>A short note on what happened at this step.</div>
</section>

<!-- 26 Q&A -->
<section class="slide">
  <div class="a brand-dot"></div><div class="a brand-side">Ledger Lanternfox</div><div class="a pg">26</div>
  <div class="a title center" style="left:0;width:388px;top:20px">Q&amp;A Slide</div>
  <div class="a bar" style="left:186px;top:41px"></div>
  <div class="a q" style="left:51px;top:63px;background:var(--navy)">Q</div><div class="a q" style="left:51px;top:94px;background:var(--navy)">Q</div><div class="a q" style="left:51px;top:126px;background:var(--navy)">Q</div><div class="a q" style="left:51px;top:157px;background:var(--navy)">Q</div>
  <div class="a q" style="left:222px;top:63px;background:var(--red)">A</div><div class="a q" style="left:222px;top:94px;background:var(--red)">A</div><div class="a q" style="left:222px;top:126px;background:var(--red)">A</div><div class="a q" style="left:222px;top:157px;background:var(--red)">A</div>
  <div class="a tx" style="left:83px;top:63px;width:90px">Write a common question from the audience here.</div>
  <div class="a tx" style="left:83px;top:94px;width:90px">Write a common question from the audience here.</div>
  <div class="a tx" style="left:83px;top:126px;width:90px">Write a common question from the audience here.</div>
  <div class="a tx" style="left:83px;top:157px;width:90px">Write a common question from the audience here.</div>
  <div class="a tx" style="left:254px;top:63px;width:90px">Give a short and clear answer to it right here.</div>
  <div class="a tx" style="left:254px;top:94px;width:90px">Give a short and clear answer to it right here.</div>
  <div class="a tx" style="left:254px;top:126px;width:90px">Give a short and clear answer to it right here.</div>
  <div class="a tx" style="left:254px;top:157px;width:90px">Give a short and clear answer to it right here.</div>
</section>

<!-- 27 thank you -->
<section class="slide" style="background:#f6f7f9">
  <div class="a brand brand-navy" style="left:44px;top:57px;font-size:8px"><i style="width:10px;height:10px;background:var(--navy)"></i>Ledger Lanternfox</div>
  <div class="a" style="left:43px;top:81px;width:103px;height:25px;background:var(--navy)"></div>
  <div class="a" style="left:43px;top:108px;width:103px;height:25px;background:#fff"></div>
  <div class="a" style="left:43px;top:135px;width:103px;height:25px;background:#fff"></div>
  <svg class="a" style="left:0;top:0" width="388" height="217"><g fill="none" stroke-width=".8"><circle cx="59" cy="93" r="4" stroke="#fff"/><path d="M55 93h8M59 89v8" stroke="#fff"/><path d="M55 118l4 4 4-6" stroke="var(--navy)"/><rect x="55" y="144" width="8" height="6" stroke="var(--navy)"/></g></svg>
  <div class="a tx-w" style="left:73px;top:91px">www.website.com</div>
  <div class="a tx" style="left:73px;top:115px">Here to write your<br>Company adress</div>
  <div class="a tx" style="left:73px;top:145px">info@website.com</div>
  <div class="a" style="left:200px;top:91px;font-size:21px;font-weight:600;color:var(--navy)">THANK YOU</div>
</section>

<!-- 28 questions -->
<section class="slide">
  <div class="a brand-dot"></div><div class="a brand-side">Ledger Lanternfox</div><div class="a pg">28</div>
  <svg class="a" style="left:0;top:0" width="388" height="217">
    <path d="M90 49 L320 34 L300 177 L145 170 L135 202 L125 168 L100 165 Z" fill="none" stroke="var(--red)" stroke-width="1"/>
    <path d="M95 54 L326 39 L305 182 L148 175 L138 206 L128 172 L106 170 Z" fill="none" stroke="var(--navy)" stroke-width="1"/>
    <path d="M112 60 L304 48 L286 166 L150 160 L140 185 L132 158 L122 157 Z" fill="#fff" style="filter:drop-shadow(0 2px 4px rgba(0,0,0,.18))"/>
  </svg>
  <div class="a" style="left:146px;top:96px;font-size:21px;font-weight:600;color:var(--navy)">Questions?</div>
</section>

</main>
</body>
</html>
```